KorvaNest - Home Income and Business Resources Platform

I am looking for a website template for a multi-purposed website. This website will feature:

1.) Website Directory with Ratings & comments on listings
2.) Company Blog
3.) Homepage with Content (see files for homepage mock)

I would like the Design to have a default width 1170px (wider then normal)

Of course I am looking for Pages for Listings to be designed.

Great looking BLOG Layout: http://journal.plimworks.example/html/blog.html

I would like 4 Versions of a Website Directory Listing "Box"
1.) Basic Listing Box
2.) Sponsored Listing Box
3.) Recommended Listing Box
4.) Stay Away From Listing Box

Information on the Listing Page (Like on a Category Page)
Site Name, Site URL, Website Image, # of Views, Rating and # of Comments

Information on the Listing Details Page:
Same as ABOVE + About website Description, Vornic Score, Category Information

Decent looking examples is here: https://samples.trevolin.example/directory/computers/ and http://www.zqrankhub.example/.

I will include some sketches and screenshots of things I like/looking for. As designers,you have creative freedom and are encouraged to show this. This is Phase one of this project and winning designer is guaranteed to have future work for this project.

Target Market(s)

Directory, business, websites

Industry/Entity Type

Business

Coding

Coded - Design and coding required

Number of Pages Required

5+ page

Font styles to use
Sans Serif

Colors

Designer to choose colors to be used in the design.

Requirements
Must have
• Professional yet clean look. The use of Icons & images
• Unique Look
Should not have
• Any exact copies of any examples I provided

```html
<!DOCTYPE html>
<html lang="en">
<head>
<meta charset="utf-8">
<title>KorvaNest – About Us</title>
<link rel="stylesheet" href="https://fonts.googleapis.com/css2?family=Poppins:wght@700&family=Roboto+Condensed:wght@400;700&family=Open+Sans:wght@400&display=swap">
<style>
  :root{
    --sky-light:#93d0e6;
    --sky-mid:#5fb3d8;
    --sky-deep:#3f86c0;
    --white:#ffffff;
    --ink:#333333;
    --body:#3d3d3d;
    --accent:#5ec3e2;
    --panel:#f6f7f8;
    --panel-line:#e4e6e8;
    --logo-grey:#9a9a9a;
    --ad-cream:#efe3c4;
    --ad-orange:#fb5a22;
  }
  *{margin:0;padding:0;box-sizing:border-box}
  html,body{width:1200px;height:1007px;overflow:hidden}
  body{
    position:relative;
    background:
      linear-gradient(160deg,rgba(255,255,255,.18) 0%,rgba(255,255,255,0) 40%),
      linear-gradient(135deg,var(--sky-light) 0%,var(--sky-mid) 45%,var(--sky-deep) 100%);
    font-family:"Open Sans",Arial,sans-serif;
    color:var(--body);
  }
  .brand{
    position:absolute;left:99px;top:32px;
    font-family:"Poppins",Arial,sans-serif;font-weight:700;font-size:40px;
    color:var(--white);letter-spacing:.5px;
  }
  .main-nav{position:absolute;top:43px;right:98px;display:flex;align-items:center}
  .main-nav a{
    font-family:"Roboto Condensed",Arial,sans-serif;font-size:16px;color:var(--white);
    text-decoration:none;padding:6px 8px;margin-left:14px;border:1px solid transparent;border-radius:3px;
    line-height:18px;
  }
  .main-nav a.is-active{border-color:var(--white);padding:6px 11px}
  .content-card{
    position:absolute;left:81px;top:113px;width:1038px;height:716px;
    background:var(--white);border-radius:26px;box-shadow:0 2px 10px rgba(0,0,0,.15);
  }
  .page-hero{
    position:absolute;left:18px;top:17px;width:762px;height:229px;
    background:linear-gradient(135deg,#8c93a6 0%,#5f6a82 45%,#3b4561 100%);
    display:flex;align-items:center;justify-content:center;
  }
  .page-hero h1{
    font-family:"Roboto Condensed",Arial,sans-serif;font-weight:700;font-size:40px;color:var(--white);
    letter-spacing:.5px;margin-left:-2px;
  }
  .intro-image{
    position:absolute;left:19px;top:293px;width:257px;height:268px;
    background:radial-gradient(circle at 48% 38%,#6a9ed8 0%,#1f3c70 35%,#0b1733 80%);
  }
  .intro-title{
    position:absolute;left:309px;top:294px;
    font-family:"Roboto Condensed",Arial,sans-serif;font-weight:400;font-size:31px;color:var(--ink);
  }
  .intro-text{position:absolute;left:308px;top:343px;width:470px}
  .intro-text p,.full-text{font-size:11.6px;line-height:20.6px;color:var(--body)}
  .intro-text p+p{margin-top:10px}
  .full-text{position:absolute;left:20px;top:585px;width:760px}
  .sponsor-panel{
    position:absolute;left:806px;top:17px;width:214px;height:284px;
    background:var(--panel);border:1px solid var(--panel-line);
  }
  .sponsor-head{
    height:39px;background:var(--accent);color:var(--white);
    display:flex;align-items:center;justify-content:space-between;padding:0 14px;
    font-family:"Roboto Condensed",Arial,sans-serif;font-size:19px;
  }
  .sponsor-list{list-style:none;text-align:center;padding-top:23px}
  .sponsor-list li{
    font-family:"Roboto Condensed",Arial,sans-serif;font-size:25px;color:var(--logo-grey);
    height:52px;line-height:52px;
  }
  .ad-slot{position:absolute;left:806px;width:214px}
  .ad-slot.cream{top:327px;height:162px;background:var(--ad-cream);border:1px solid #e49a7a}
  .ad-slot.orange{top:516px;height:181px;background:var(--ad-orange)}
  .site-footer{position:absolute;left:0;top:878px;width:1200px;text-align:center;color:var(--white)}
  .social-list{display:flex;justify-content:center;gap:13px;list-style:none}
  .social-list li{width:24px;height:24px;border-radius:4px;background:var(--white)}
  .footer-nav{margin-top:16px;font-size:13px}
  .footer-nav a{color:var(--white);text-decoration:none}
  .footer-nav span{margin:0 9px}
  .copyright{margin-top:13px;font-size:12.5px}
</style>
</head>
<body>
  <header>
    <div class="brand">KorvaNest</div>
    <nav class="main-nav">
      <a href="#">HOME</a>
      <a href="#" class="is-active">ABOUT US</a>
      <a href="#">OUR SERVICES</a>
      <a href="#">BLOG</a>
      <a href="#">CONTACT US</a>
    </nav>
  </header>

  <main class="content-card">
    <section class="page-hero" role="img" aria-label="Photo of a business team meeting in an office">
      <h1>ABOUT US</h1>
    </section>

    <div class="intro-image" role="img" aria-label="Illustration of a glowing light bulb above an open hand"></div>
    <h2 class="intro-title">WELCOME TO KORVANEST</h2>
    <div class="intro-text">
      <p>Sed ut perspiciatis unde omnis iste natus error sit voluptatem accusantium doloremque laudantium, totam rem aperiam, eaque ipsa quae ab illo inventore veritatis et quasi architecto beatae vitae dicta sunt explicabo. Nemo enim ipsam voluptatem quia voluptas sit aspernatur aut odit aut fugit, sed quia consequuntur magni dolores eos qui ratione voluptatem sequi nesciunt.</p>
      <p>Nemo enim ipsam voluptatem quia voluptas sit aspernatur aut odit aut fugit, sed quia consequuntur magni dolores eos qui ratione voluptatem sequi nesciunt. Neque porro quisquam est, qui dolorem ipsum quia dolor sit amet, consectetur, adipisci velit, sed quia non numquam eius modi tempora incidunt ut labore et dolore magnam aliquam quaerat voluptatem. Ut enim ad minima veniam,</p>
    </div>
    <p class="full-text">Nemo enim ipsam voluptatem quia voluptas sit aspernatur aut odit aut fugit, sed quia consequuntur magni dolores eos qui ratione voluptatem sequi nesciunt. Neque porro quisquam est, qui dolorem ipsum quia dolor sit amet, consectetur, adipisci velit, sed quia non numquam eius modi tempora incidunt ut labore et dolore magnam aliquam quaerat voluptatem. Ut enim ad minima veniam,</p>

    <aside>
      <div class="sponsor-panel">
        <div class="sponsor-head">
          <svg width="9" height="14" viewBox="0 0 9 14"><path d="M7 1 1 7l6 6" fill="none" stroke="#fff" stroke-width="2"/></svg>
          <span>SPONSORED</span>
          <svg width="9" height="14" viewBox="0 0 9 14"><path d="M2 1l6 6-6 6" fill="none" stroke="#fff" stroke-width="2"/></svg>
        </div>
        <ul class="sponsor-list">
          <li>Lumavet</li>
          <li>Brenwick</li>
          <li>Tolvara</li>
          <li>Fernly</li>
        </ul>
      </div>
      <div class="ad-slot cream" role="img" aria-label="Cartoon banner advertisement on a cream background"></div>
      <div class="ad-slot orange" role="img" aria-label="Illustrated banner advertisement on an orange background"></div>
    </aside>
  </main>

  <footer class="site-footer">
    <ul class="social-list">
      <li aria-label="Social profile"></li>
      <li aria-label="Social profile"></li>
      <li aria-label="Social profile"></li>
      <li aria-label="Social profile"></li>
      <li aria-label="Social profile"></li>
    </ul>
    <nav class="footer-nav">
      <a href="#">Home</a><span>/</span><a href="#">Contact</a><span>/</span><a href="#">services</a><span>/</span><a href="#">About Us</a><span>/</span><a href="#">Discussion</a><span>/</span><a href="#">Videos Links</a>
    </nav>
    <p class="copyright">Copyright @ 2017 KorvaNest. All Rights Reserved.</p>
  </footer>
</body>
</html>
```